BildeVOLD buisnesscard

Hey :) I need a modern buisnesscard for my company BildeVOLD
It most have:
Dagligleder og Fotograf: Henrik Audun Strandvik

Mob: +4791264085
Epost: post@bildevold.example
Adresse: Kvernbakken9, 6040 Solvika

Facbook and instagram logo with text BildeVOLD

BildeVOLD logo

It Company

```html
<!DOCTYPE html>
<html lang="no">
<head>
<meta charset="utf-8">
<title>BildeVOLD – visittkort</title>
<link href="https://fonts.googleapis.com/css2?family=Noto+Sans:wght@400;600&display=swap" rel="stylesheet">
<style>
  :root {
    --page: #e4e4e4;
    --card: #262626;
    --ink: #a6a6a6;
    --ink-soft: #9a9a9a;
    --frame: #bdbdbd;
  }
  * { box-sizing: border-box; margin: 0; padding: 0; }
  html, body { width: 1200px; height: 1200px; overflow: hidden; }
  body {
    background: var(--page);
    font-family: "Noto Sans", Verdana, sans-serif;
    position: relative;
  }
  .card {
    position: absolute;
    left: 240px;
    width: 720px;
    height: 434px;
    background: var(--card);
    color: var(--ink);
    box-shadow: 0 6px 14px rgba(0,0,0,.25);
  }
  .card--front { top: 106px; }
  .card--back { top: 624px; }

  .corner { position: absolute; width: 42px; height: 42px; border-color: var(--frame); border-style: solid; border-width: 0; }
  .corner--tl { left: 24px; top: 24px; border-left-width: 1.5px; border-top-width: 1.5px; }
  .corner--tr { right: 24px; top: 24px; border-right-width: 1.5px; border-top-width: 1.5px; }
  .corner--bl { left: 24px; bottom: 24px; border-left-width: 1.5px; border-bottom-width: 1.5px; }
  .corner--br { right: 24px; bottom: 24px; border-right-width: 1.5px; border-bottom-width: 1.5px; }

  .brand {
    position: absolute;
    left: 66px;
    top: 194px;
    width: 240px;
    text-align: center;
    font-weight: 600;
    font-size: 34px;
    letter-spacing: .5px;
    color: var(--ink);
  }

  .person { position: absolute; left: 350px; top: 100px; }
  .person__name { font-size: 25px; font-weight: 400; color: var(--ink); letter-spacing: .3px; }
  .person__role { font-size: 16px; margin-top: 2px; color: var(--ink-soft); letter-spacing: .3px; }

  .contact { position: absolute; left: 352px; top: 184px; list-style: none; }
  .contact__item { display: flex; align-items: flex-start; font-size: 18px; line-height: 23px; letter-spacing: .4px; }
  .contact__item + .contact__item { margin-top: 14px; }
  .contact__item--phone { margin-top: 13px; }
  .contact__icon { width: 23px; height: 23px; flex: none; margin-right: 23px; }

  .back-name {
    position: absolute;
    left: 0; right: 0;
    top: 145px;
    text-align: center;
    font-weight: 600;
    font-size: 64px;
    letter-spacing: 1px;
    color: var(--ink);
  }
  .social { position: absolute; left: 0; right: 0; top: 334px; display: flex; justify-content: center; gap: 26px; }
  .social__item { display: flex; align-items: center; font-size: 19px; letter-spacing: .4px; }
  .social__mark { width: 32px; height: 32px; border: 1.8px solid var(--ink); border-radius: 50%; margin-right: 12px; }
</style>
</head>
<body>

<section class="card card--front">
  <span class="corner corner--tl"></span><span class="corner corner--tr"></span>
  <span class="corner corner--bl"></span><span class="corner corner--br"></span>

  <div class="brand">BildeVOLD</div>

  <div class="person">
    <h1 class="person__name">Henrik Audun Strandvik</h1>
    <p class="person__role">Dagligleder og Fotograf</p>
  </div>

  <ul class="contact">
    <li class="contact__item">
      <svg class="contact__icon" viewBox="0 0 24 24"><circle cx="12" cy="12" r="12" fill="var(--ink)"/><path d="M12 5.5a4 4 0 0 0-4 4c0 3 4 8 4 8s4-5 4-8a4 4 0 0 0-4-4z" fill="var(--card)"/><circle cx="12" cy="9.5" r="1.5" fill="var(--ink)"/></svg>
      <span>Kvernbakken9<br>6040 Solvika</span>
    </li>
    <li class="contact__item contact__item--phone">
      <svg class="contact__icon" viewBox="0 0 24 24"><circle cx="12" cy="12" r="12" fill="var(--ink)"/><path d="M8.5 6.5l2 0 1 3-1.4 1.1a8 8 0 0 0 3.3 3.3l1.1-1.4 3 1 0 2a1.5 1.5 0 0 1-1.6 1.5A10 10 0 0 1 7 8.1 1.5 1.5 0 0 1 8.5 6.5z" fill="var(--card)"/></svg>
      <span>912 64 085</span>
    </li>
    <li class="contact__item">
      <svg class="contact__icon" viewBox="0 0 24 24"><circle cx="12" cy="12" r="12" fill="var(--ink)"/><circle cx="12" cy="12" r="6.5" fill="none" stroke="var(--card)" stroke-width="1.6"/><path d="M5.5 12h13M12 5.5c-2.5 3-2.5 10 0 13M12 5.5c2.5 3 2.5 10 0 13" fill="none" stroke="var(--card)" stroke-width="1.4"/></svg>
      <span>www.bildevold.example</span>
    </li>
    <li class="contact__item">
      <svg class="contact__icon" viewBox="0 0 24 24"><circle cx="12" cy="12" r="12" fill="var(--ink)"/><rect x="6" y="8" width="12" height="8.5" fill="var(--card)"/><path d="M6 8l6 5 6-5" fill="none" stroke="var(--ink)" stroke-width="1.3"/></svg>
      <span>post@bildevold.example</span>
    </li>
  </ul>
</section>

<section class="card card--back">
  <span class="corner corner--tl"></span><span class="corner corner--tr"></span>
  <span class="corner corner--bl"></span><span class="corner corner--br"></span>

  <div class="back-name">BildeVOLD</div>

  <div class="social">
    <div class="social__item"><span class="social__mark"></span>BildeVOLD</div>
    <div class="social__item"><span class="social__mark"></span>BildeVOLD</div>
  </div>
</section>

</body>
</html>
```